we are an outdoor outlet in a country club that has a variety of outlets. The Club is called Meadowlark and is located in Cairo, Egypt. This garden menu will include cuisines from the Mediterranean, Asia and Texmex. we need a menu that is colorful and would fit an A3 size, back and front are to be used. Attached is the old menu currently in use (Garden Menu 2012.pdf is just for reference) and the new menu text for you to use is under the name Garden Menu Fall 2013
thank you.
Updates
Logo files have been uploaded for this project
Industry/Entity Type
Club
Look and feel
Each slider illustrates characteristics of the customer's brand and the style your logo design should communicate.

```html
<!DOCTYPE html>
<html lang="en">
<head>
<meta charset="utf-8">
<title>Garden Menu – Meadowlark</title>
<link href="https://fonts.googleapis.com/css2?family=Source+Sans+3:wght@300;400;600;700&family=Nunito:wght@800&family=Noto+Serif:wght@400&display=swap" rel="stylesheet">
<style>
:root{
  --paper:#f1dfb4;
  --paper-light:#f8ecce;
  --maroon:#82282c;
  --ink:#8b3a2e;
  --desc:#b4452c;
  --ribbon:#c5482a;
  --ribbon-dark:#8f2f1a;
  --leaf:#c9cc55;
  --leaf-dark:#9ea03a;
  --gold:#d9a84a;
  --panel:#f8d64c;
  --panel-light:#fbe277;
  --badge:#6e4a3b;
  --frame:#ffffff;
}
*{box-sizing:border-box;margin:0;padding:0}
html,body{width:848px;height:1200px;overflow:hidden;background:#fff}
.menu{position:relative;width:848px;height:1200px;overflow:hidden;
  background:radial-gradient(ellipse at 50% 45%,var(--paper-light) 0%,var(--paper) 75%);
  font-family:"Source Sans 3",Arial,sans-serif;color:var(--ink)}
.frame{position:absolute;border:2px solid var(--frame)}
.frame.outer{left:22px;top:30px;right:28px;bottom:32px}
.frame.inner{left:28px;top:36px;right:34px;bottom:38px;border-width:1px;opacity:.7}
.top-band{position:absolute;left:30px;top:38px;right:36px;height:82px;background:rgba(255,250,235,.55)}
.title{position:absolute;left:102px;top:50px;font-weight:700;font-size:50px;letter-spacing:.5px;color:var(--maroon);line-height:1}
.brand{position:absolute;left:568px;top:64px;display:flex;align-items:center;gap:8px}
.brand-dot{width:22px;height:22px;border-radius:50%;background:var(--leaf)}
.brand-name{font-family:"Source Sans 3",Arial,sans-serif;font-weight:400;font-size:26px;color:var(--ink)}
.ribbon{position:absolute;left:98px;top:128px}
.ribbon-label{position:absolute;left:210px;top:133px;width:428px;text-align:center;color:#fff;font-weight:400;font-size:28px;letter-spacing:.5px}
.heading{position:absolute;font-family:"Nunito",Arial,sans-serif;font-weight:800;color:var(--maroon);text-align:center;font-size:19px;line-height:1}
.rule{position:absolute;height:1px;background:var(--gold)}
.sprig{position:absolute;width:12px;height:10px;border-radius:50% 50% 2px 2px;background:var(--gold)}
.item{position:absolute;font-size:12.3px;line-height:1.15;text-transform:uppercase;color:var(--ink)}
.item .desc{display:block;text-transform:none;font-family:"Noto Serif",Georgia,serif;font-size:9.3px;color:var(--desc);margin-top:2px}
.price{position:absolute;font-size:12.3px;color:var(--ink)}
.sub{font-size:9.5px;color:var(--desc);line-height:1.3}
.sub .opt{text-transform:none}
.bullet{display:inline-block;width:6px;height:6px;border-radius:50%;background:var(--ribbon);margin-right:6px;vertical-align:1px}
.subprice{position:absolute;font-size:9.5px;color:var(--desc)}
.note{position:absolute;text-align:center;font-family:"Noto Serif",Georgia,serif;font-size:9px;color:var(--ink)}
.plain{text-transform:none;font-size:12.3px}
.panel{position:absolute;left:462px;top:634px;width:342px;height:488px;border-radius:16px;background:var(--panel);box-shadow:3px 4px 6px rgba(120,80,20,.3)}
.panel-inner{position:absolute;left:8px;top:8px;right:8px;bottom:8px;border-radius:12px;border:1.5px dashed rgba(255,255,255,.85)}
.panel .heading{font-size:24px}
.main{position:absolute;left:26px;font-size:15px;color:var(--maroon);line-height:1.1;text-transform:uppercase}
.main .desc{display:block;text-transform:none;font-family:"Noto Serif",Georgia,serif;font-size:11px;color:var(--desc);line-height:1.35;margin-top:3px}
.main-price{position:absolute;right:32px;font-size:15px;color:var(--maroon)}
.sauces .desc span{display:block}
.olives{position:absolute;left:414px;top:634px;width:102px;height:76px;border-radius:40px 40px 40px 10px;background:linear-gradient(135deg,#8a6a4a,#4a3526);transform:rotate(-14deg)}
.badge{position:absolute;left:391px;top:1070px;width:94px;height:94px;border-radius:50%;background:var(--badge);display:flex;align-items:center;justify-content:center}
.badge::before{content:"";position:absolute;inset:5px;border-radius:50%;border:1px dashed rgba(255,255,255,.7)}
.badge p{color:#fff;font-family:"Noto Serif",Georgia,serif;font-size:7.4px;line-height:1.25;text-align:center;width:70px}
.badge b{font-weight:700}
</style>
</head>
<body>
<div class="menu">
  <div class="top-band"></div>
  <div class="frame outer"></div>
  <div class="frame inner"></div>

  <h1 class="title">GARDEN MENU</h1>
  <div class="brand"><span class="brand-dot"></span><span class="brand-name">meadowlark</span></div>

  <svg class="ribbon" width="680" height="64" viewBox="0 0 680 64" aria-hidden="true">
    <polygon points="0,14 140,14 140,58 0,58 22,36" fill="var(--leaf)"/>
    <polygon points="680,14 540,14 540,58 680,58 658,36" fill="var(--leaf)"/>
    <polygon points="110,44 540,44 560,58 120,58" fill="#b9b3a3" opacity=".7"/>
    <polygon points="112,44 140,58 140,44" fill="var(--leaf-dark)"/>
    <polygon points="538,44 510,58 538,58" fill="var(--leaf-dark)"/>
    <rect x="112" y="2" width="428" height="42" fill="var(--ribbon)"/>
  </svg>
  <div class="ribbon-label">MEDITERRANEAN CORNER</div>

  <!-- Appetizers -->
  <div class="heading" style="left:100px;top:198px;width:280px">appetizers</div>
  <div class="rule" style="left:100px;top:228px;width:280px"></div>
  <div class="sprig" style="left:234px;top:223px"></div>

  <div class="item" style="left:100px;top:239px">Turkish Brioche<span class="desc">Filled with seasoned chicken and basmati rice</span></div><div class="price" style="left:370px;top:239px">00</div>
  <div class="item" style="left:100px;top:278px">Roasted Eggplant Rolls<span class="desc">With herbed ricotta cheese and pine nuts</span></div><div class="price" style="left:370px;top:278px">00</div>
  <div class="item" style="left:100px;top:317px">Falafel in Mini Pita<span class="desc">Served with tehina and oriental salsa</span></div><div class="price" style="left:370px;top:317px">00</div>
  <div class="item" style="left:100px;top:355px">Mankousha<span class="desc">With thyme and olive oil</span></div><div class="price" style="left:370px;top:355px">00</div>
  <div class="item" style="left:100px;top:394px">Fried Kobeba<span class="desc">With minced meat, spices, and pine nuts</span></div><div class="price" style="left:370px;top:394px">00</div>
  <div class="item" style="left:100px;top:433px">Fried Calamari a la Romana<span class="desc">Served with aioli</span></div><div class="price" style="left:370px;top:433px">00</div>
  <div class="item" style="left:100px;top:472px">Samboussek<span class="desc">With herbed white cheese and mint</span></div><div class="price" style="left:370px;top:472px">00</div>
  <div class="item" style="left:100px;top:510px">Oriental Sausage<span class="desc">Sautéed with garlic and onion</span></div><div class="price" style="left:370px;top:510px">00</div>
  <div class="item" style="left:100px;top:549px">Mini Vine Leaves<span class="desc">With a yoghurt dip</span></div><div class="price" style="left:370px;top:549px">00</div>
  <div class="item" style="left:100px;top:588px">Fatouch<span class="desc">With a pomegranate syrup dressing</span></div><div class="price" style="left:370px;top:588px">00</div>
  <div class="item" style="left:100px;top:627px">Hummus<span class="desc">Seasoned with lemon juice, garlic, and olive oil</span></div><div class="price" style="left:370px;top:627px">00</div>
  <div class="item" style="left:100px;top:665px">White Cheese<span class="desc">With diced tomato, thyme, and olive oil</span></div><div class="price" style="left:370px;top:665px">00</div>
  <div class="item" style="left:100px;top:704px">Tehina<span class="desc">Seasoned with cumin, lemon juice, and garlic</span></div><div class="price" style="left:370px;top:704px">00</div>

  <!-- Sandwiches -->
  <div class="heading" style="left:100px;top:737px;width:280px">sandwiches</div>
  <div class="note" style="left:100px;top:757px;width:280px">(Served with french fries or garden salad)</div>
  <div class="rule" style="left:100px;top:778px;width:280px"></div>
  <div class="sprig" style="left:234px;top:773px"></div>

  <div class="item" style="left:100px;top:793px">Beef or Chicken Shawerma</div><div class="price" style="left:370px;top:793px">00</div>
  <div class="item" style="left:100px;top:819px">Grilled Kofta</div><div class="price" style="left:370px;top:819px">00</div>
  <div class="item" style="left:100px;top:845px">Greek Lamb Gyro<span class="desc">in pita bread with Tzatziki</span></div><div class="price" style="left:370px;top:845px">00</div>
  <div class="item" style="left:100px;top:883px">Club Sandwich<span class="desc">with smoked beef, turkey, egg</span></div><div class="price" style="left:370px;top:883px">00</div>

  <!-- Pizza & pasta -->
  <div class="heading" style="left:100px;top:924px;width:280px">pizza &amp; pasta</div>
  <div class="rule" style="left:100px;top:953px;width:280px"></div>
  <div class="sprig" style="left:234px;top:948px"></div>

  <div class="item" style="left:100px;top:964px">Pizza Margarita <span class="plain">(Choose your toppings)</span>
    <div class="sub"><span class="bullet"></span><span class="opt">Bell Peppers, Olives, Tomato, Onion</span></div>
    <div class="sub"><span class="bullet"></span><span class="opt">Mushroom, Chicken, Tuna, Pepperoni</span></div>
    <div class="sub"><span class="bullet"></span><span class="opt">Smoked Salmon, Shrimps</span></div>
  </div>
  <div class="price" style="left:370px;top:964px">00</div>
  <div class="subprice" style="left:372px;top:979px">00</div>
  <div class="subprice" style="left:372px;top:991px">00</div>
  <div class="subprice" style="left:372px;top:1004px">00</div>

  <div class="item" style="left:100px;top:1026px">Create Your Own Pasta
    <div class="sub">TYPE &nbsp;&nbsp;&nbsp;&nbsp;&nbsp;&nbsp;: <span class="opt">Spaghetti, Tagliatelle, Penne</span></div>
    <div class="sub">SAUCES : <span class="opt">Napolitana, Bolognese, Alfredo</span></div>
    <div class="plain">(Choose your toppings)</div>
  </div>
  <div class="price" style="left:370px;top:1026px">00</div>
  <div class="subprice" style="left:372px;top:1040px">00</div>
  <div class="subprice" style="left:372px;top:1052px">00</div>

  <div class="item" style="left:100px;top:1094px">Lasagna</div><div class="price" style="left:370px;top:1094px">00</div>

  <!-- Soups -->
  <div class="heading" style="left:460px;top:198px;width:282px">soups</div>
  <div class="rule" style="left:460px;top:228px;width:282px"></div>
  <div class="sprig" style="left:596px;top:223px"></div>

  <div class="item" style="left:460px;top:239px">Tomato Basil<span class="desc">Simmered tomato soup finished with<br>fresh basil and cream</span></div><div class="price" style="left:732px;top:239px">00</div>
  <div class="item" style="left:460px;top:290px">Chicken Cream<span class="desc">Chicken broth with roasted chicken cubes,<br>pine nuts, and cream</span></div><div class="price" style="left:732px;top:290px">00</div>
  <div class="item" style="left:460px;top:340px">Moroccan Harira<span class="desc">Vegetable broth with fresh tomato,<br>chickpeas, lentil, cilantro, and diced lamb</span></div><div class="price" style="left:732px;top:340px">00</div>

  <!-- Salads -->
  <div class="heading" style="left:460px;top:391px;width:282px">salads</div>
  <div class="rule" style="left:460px;top:420px;width:282px"></div>
  <div class="sprig" style="left:596px;top:415px"></div>

  <div class="item" style="left:460px;top:434px">Caprese<span class="desc">Buffalo mozzarella and sliced tomato<br>with a balsamic vinaigrette</span></div><div class="price" style="left:732px;top:434px">00</div>
  <div class="item" style="left:460px;top:485px">Rocket Apple<span class="desc">Rocket leaves with gorgonzola, croutons,<br>and strawberry vinaigrette</span></div><div class="price" style="left:732px;top:485px">00</div>
  <div class="item" style="left:460px;top:535px">French Riviera Nicoise<span class="desc">Lettuce, egg, tomato, tuna, olives, onion,<br>celery, radish, bell pepper in a French vinaigrette</span></div><div class="price" style="left:732px;top:535px">00</div>
  <div class="item" style="left:460px;top:586px">Folle<span class="desc">Mixed greens with crab sticks, mushroom,<br>corn, cherry tomato in a mango vinaigrette</span></div><div class="price" style="left:732px;top:586px">00</div>

  <!-- Main courses -->
  <section class="panel">
    <div class="panel-inner"></div>
    <div class="heading" style="left:0;top:24px;width:342px">main courses</div>
    <div class="rule" style="left:26px;top:59px;width:286px;background:var(--ribbon)"></div>
    <div class="sprig" style="left:165px;top:54px;background:var(--ribbon)"></div>

    <div class="main" style="top:78px">Veal Parmeggiana<span class="desc">Breaded veal escalope topped with<br>melted cheese and tomato sauce<br>served with Spaghetti</span></div><div class="main-price" style="top:78px">00</div>
    <div class="main" style="top:153px">Chicken a la Francaise<span class="desc">Pan fried chicken breast in a mushroom<br>cream sauce with vegetables white rice</span></div><div class="main-price" style="top:153px">00</div>
    <div class="main" style="top:214px">Grilled Salmon<span class="desc">Salmon steak charcoal grilled with avocado<br>tomato relish and creamy mushroom risotto</span></div><div class="main-price" style="top:214px">00</div>
    <div class="main" style="top:278px">Moroccan Chicken<span class="desc">Chicken cubes simmered with spices<br>and olives served with tomato rice</span></div><div class="main-price" style="top:278px">00</div>
    <div class="main" style="top:340px">Filet<span class="desc">Tender filet grilled to your liking served with<br>mashed potato and creamed spinach</span></div><div class="main-price" style="top:340px">00</div>
    <div class="main sauces" style="top:404px">Choice of Sauces<span class="desc"><span><i class="bullet"></i>Brown Mushroom</span><span><i class="bullet"></i>Green Peppercorn</span><span><i class="bullet"></i>Gorgonzola</span></span></div>
  </section>

  <div class="olives" role="img" aria-label="Illustration of an olive branch with olives"></div>

  <div class="badge"><p>PRICES ARE SUBJECT TO <b>12% SERVICE CHARGE &amp; 10% SALES TAX</b></p></div>
</div>
</body>
</html>
```